Professional & attention grabbing.

A business card design, front and back. I already have a logo I will attach, but I am open to something new as well.
Things to include:
Name:
Title:
Phone:
Email:
Wanting something that is professional but attention grabbing.
Also we do a lot of work using drones on natural gas pipelines (leading the future)if you want to include any of that. I'm open to ideas.
Target Market(s)
Natural gas transmission industry / greenhouse gas mitigation industry
Industry/Entity Type
Business
Colors
Designer to choose colors to be used in the design.
Look and feel
Each slider illustrates characteristics of the customer's brand and the style your logo design should communicate.

```html
<!DOCTYPE html>
<html lang="en">
<head>
<meta charset="UTF-8">
<title>Keystone Inspections – Business Card</title>
<link href="https://fonts.googleapis.com/css2?family=Roboto+Condensed:wght@400;700&display=swap" rel="stylesheet">
<style>
  :root {
    --brand-red: #d3222a;
    --brand-red-deep: #b81d24;
    --charcoal: #3a3a3c;
    --slate: #6b6b6e;
    --paper: #ffffff;
    --backdrop: #e9e6e1;
  }
  * { box-sizing: border-box; margin: 0; padding: 0; }
  html, body {
    width: 1200px; height: 950px; overflow: hidden;
    background: var(--backdrop);
    font-family: "Roboto Condensed", Arial, sans-serif;
  }
  .canvas { position: relative; width: 1200px; height: 950px; }
  .card {
    position: absolute; left: 250px; width: 700px; height: 400px;
    border-radius: 22px; overflow: hidden;
    box-shadow: 0 6px 18px rgba(0,0,0,.18);
  }
  .card-front { top: 50px; background: var(--paper); }
  .card-back { top: 500px; background: var(--brand-red); }

  .front-swoosh { position: absolute; right: 0; top: 0; width: 700px; height: 400px; }

  .brand { position: absolute; left: 60px; top: 100px; display: flex; align-items: center; gap: 14px; }
  .brand-mark { width: 40px; height: 40px; background: var(--brand-red); }
  .brand-name {
    font-weight: 700; font-size: 40px; color: var(--charcoal);
    text-transform: uppercase; letter-spacing: 1px; line-height: 1;
  }

  .person { position: absolute; left: 60px; top: 230px; width: 200px; text-align: right; }
  .person-name { color: var(--brand-red); font-weight: 400; font-size: 28px; text-transform: uppercase; letter-spacing: .5px; }
  .person-title { color: var(--charcoal); font-size: 19px; margin-top: 4px; }

  .divider { position: absolute; left: 282px; top: 222px; width: 1px; height: 86px; background: #bdbdbd; }

  .contact { position: absolute; left: 302px; top: 224px; list-style: none; }
  .contact li { display: flex; align-items: center; gap: 10px; color: var(--charcoal); font-size: 19px; height: 28px; }
  .contact svg { width: 14px; height: 14px; flex: none; }

  .back-pattern { position: absolute; inset: 0; background: linear-gradient(135deg, var(--brand-red) 0%, var(--brand-red-deep) 100%); }
  .back-brand { position: absolute; left: 0; right: 0; top: 150px; text-align: center; }
  .back-brand-name { color: var(--paper); font-weight: 700; font-size: 54px; text-transform: uppercase; letter-spacing: 1px; }
  .back-url { color: var(--paper); font-size: 20px; letter-spacing: 4px; margin-top: 14px; }
</style>
</head>
<body>
<main class="canvas">

  <section class="card card-front" aria-label="Card front">
    <svg class="front-swoosh" viewBox="0 0 700 400" aria-hidden="true">
      <path d="M700 0 L640 0 C590 120 660 260 560 400 L700 400 Z" fill="var(--brand-red)"/>
      <path d="M630 0 C580 120 650 260 548 400 L560 400 C660 260 590 120 640 0 Z" fill="var(--charcoal)"/>
    </svg>

    <div class="brand">
      <span class="brand-mark"></span>
      <span class="brand-name">Keystone Inspections</span>
    </div>

    <div class="person">
      <p class="person-name">Dana Mercer</p>
      <p class="person-title">CEO/Founder</p>
    </div>

    <span class="divider"></span>

    <ul class="contact">
      <li>
        <svg viewBox="0 0 16 16"><path d="M3 1 L6 1 L7 5 L5 6.5 C6 9 7.5 10.5 10 11.5 L11.5 9.5 L15 10.5 L15 13.5 C15 14.5 14 15 13 15 C6.5 14.5 1.5 9.5 1 3 C1 2 2 1 3 1 Z" fill="var(--brand-red)"/></svg>
        555 014 2290
      </li>
      <li>
        <svg viewBox="0 0 16 16"><rect x="1" y="3" width="14" height="10" rx="1" fill="var(--brand-red)"/><path d="M1.5 4 L8 9 L14.5 4" stroke="#fff" stroke-width="1.4" fill="none"/></svg>
        dana@keystoneinspect.com
      </li>
      <li>
        <svg viewBox="0 0 16 16"><circle cx="8" cy="8" r="7" fill="var(--brand-red)"/><path d="M1 8 H15 M8 1 C4 5 4 11 8 15 M8 1 C12 5 12 11 8 15" stroke="#fff" stroke-width="1" fill="none"/></svg>
        www.keystoneinspect.com
      </li>
    </ul>
  </section>

  <section class="card card-back" aria-label="Card back">
    <div class="back-pattern" role="img" aria-label="Repeating tiled pattern of the brand symbol in tonal red"></div>
    <div class="back-brand">
      <p class="back-brand-name">Keystone Inspections</p>
      <p class="back-url">www.keystoneinspect.com</p>
    </div>
  </section>

</main>
</body>
</html>
```